Thornvale Group needs a business card design

We need a new business card design using the logo recently selected in a logo competition on Pixel Bazaar. Our business is a consultancy specializing in aviation and energy and the winning business card design will promote an image of precision and professionalism with creativity.

Please use the logo with the name on the front of the card and use a complementary font. Make the back white with either the light grey or dark grey logo.

Target Market(s)

Senior finance and legal leaders at aviation and energy companies

Industry/Entity Type

Management Consulting

Contact Information for Business Card

Peter Castrell
President
Thornvale Group

www.thornvalegroup.example

(555) 204-6391
pc@thornvalegroup.example

Requirements
Must have
• Professional font that goes well with the logo font

```html
<!DOCTYPE html>
<html lang="en">
<head>
<meta charset="utf-8">
<title>Thornvale Group – Business Card</title>
<link href="https://fonts.googleapis.com/css2?family=Open+Sans:wght@400;600;700&display=swap" rel="stylesheet">
<style>
  :root {
    --bg-top: #939393;
    --bg-bottom: #747474;
    --card-white: #ffffff;
    --navy: #17416f;
    --navy-text: #1c3c6c;
    --grey-text: #5a5a5a;
    --white: #ffffff;
  }
  * { margin: 0; padding: 0; box-sizing: border-box; }
  html, body {
    width: 1200px;
    height: 900px;
    overflow: hidden;
  }
  body {
    position: relative;
    background: linear-gradient(to bottom, var(--bg-top), var(--bg-bottom));
    font-family: "Open Sans", Arial, sans-serif;
  }
  .card {
    position: absolute;
    top: 306px;
    width: 440px;
    height: 271px;
    border-radius: 10px;
  }
  .card-front { left: 149px; background: var(--card-white); }
  .card-back  { left: 608px; background: var(--navy); }

  .brand-name {
    position: absolute;
    left: 0;
    width: 228px;
    top: 115px;
    text-align: center;
    color: var(--navy-text);
    font-weight: 400;
    font-size: 22px;
    letter-spacing: 2px;
    line-height: 1.25;
  }
  .brand-name .brand-line-2 {
    display: block;
    font-size: 11px;
    letter-spacing: 11px;
    padding-left: 11px;
  }

  .contact {
    position: absolute;
    left: 243px;
    top: 92px;
    color: var(--grey-text);
  }
  .contact-name {
    color: var(--navy-text);
    font-weight: 600;
    font-size: 15px;
    line-height: 20px;
  }
  .contact-title {
    font-size: 12px;
    line-height: 16px;
  }
  .contact-list {
    list-style: none;
    margin-top: 21px;
    font-size: 12px;
    line-height: 16px;
  }
  .contact-list li {
    display: flex;
    align-items: center;
    gap: 7px;
  }
  .contact-list svg { width: 11px; height: 11px; fill: var(--navy-text); flex: none; }

  .back-brand {
    position: absolute;
    left: 0; right: 0;
    top: 92px;
    text-align: center;
    color: var(--white);
    font-weight: 400;
    font-size: 30px;
    letter-spacing: 3px;
    line-height: 1.25;
  }
  .back-brand .brand-line-2 {
    display: block;
    font-size: 14px;
    letter-spacing: 14px;
    padding-left: 14px;
  }
  .tagline {
    position: absolute;
    left: 0; right: 0;
    top: 197px;
    text-align: center;
    color: var(--white);
    font-size: 13px;
    line-height: 22px;
    letter-spacing: -0.2px;
  }
  .tagline-main { font-weight: 700; }
</style>
</head>
<body>
  <section class="card card-front" aria-label="Business card front">
    <div class="brand-name">THORNVALE<span class="brand-line-2">GROUP</span></div>
    <div class="contact">
      <p class="contact-name">Peter Castrell</p>
      <p class="contact-title">President</p>
      <ul class="contact-list">
        <li>
          <svg viewBox="0 0 24 24" aria-hidden="true"><path d="M6.6 10.8a15.1 15.1 0 0 0 6.6 6.6l2.2-2.2a1 1 0 0 1 1-.25 11.4 11.4 0 0 0 3.6.57 1 1 0 0 1 1 1V20a1 1 0 0 1-1 1A17 17 0 0 1 3 4a1 1 0 0 1 1-1h3.5a1 1 0 0 1 1 1c0 1.25.2 2.45.57 3.57a1 1 0 0 1-.25 1z"/></svg>
          (555) 204-6391
        </li>
        <li>
          <svg viewBox="0 0 24 24" aria-hidden="true"><path d="M2 5h20v14H2z M2 5l10 7 10-7" fill="none" stroke="#1c3c6c" stroke-width="0"/><path d="M2 5h20v2l-10 6L2 7zM2 9l10 6 10-6v10H2z"/></svg>
          pc@thornvalegroup.example
        </li>
      </ul>
    </div>
  </section>

  <section class="card card-back" aria-label="Business card back">
    <div class="back-brand">THORNVALE<span class="brand-line-2">GROUP</span></div>
    <div class="tagline">
      <p class="tagline-main">Finance and Strategy Consulting</p>
      <p class="tagline-sectors">Aviation | Manufacturing | Energy</p>
    </div>
  </section>
</body>
</html>
```